Letterhead for Conveyancing Company

Use existing logo to create a letterhead for a conveyancing company. Must be able to be used in Microsoft Word. Easy to read and professional.
Contact information to be at the bottom.
Bright Oak Conveyancing Pty Ltd
ACN 621 984 736PO Box 535 Campbelltown SA 5074
Mobile - 0461739286
Web address - www.brightoakconveyancing.com.au

Requirements
Must have
• Logo and contact details.
• Simple and professional.

```html
<!DOCTYPE html>
<html lang="en">
<head>
<meta charset="utf-8">
<title>Bright Oak Conveyancing – Letterhead</title>
<link rel="stylesheet" href="https://fonts.googleapis.com/css2?family=Roboto:wght@400;500&family=Great+Vibes&display=swap">
<style>
  :root{
    --backdrop:#ececec;
    --paper:#fafafa;
    --accent:#e0449a;
    --ink:#555555;
    --ink-strong:#3f3f3f;
    --brand-grey:#808080;
    --watermark:#eeeeee;
    --signature:#2f4a78;
  }
  *{margin:0;padding:0;box-sizing:border-box}
  html,body{width:1062px;height:1200px;overflow:hidden;background:var(--backdrop)}
  body{font-family:"Roboto",Arial,sans-serif;color:var(--ink)}
  .letterhead{position:absolute;left:107px;top:0;width:848px;height:1200px;background:var(--paper);overflow:hidden}
  .side-rule{position:absolute;left:0;top:0}
  .brand{position:absolute;right:53px;top:58px;text-align:right;color:var(--brand-grey);font-weight:500;line-height:1}
  .brand-name{display:block;font-size:42px;letter-spacing:-0.5px}
  .brand-sub{display:block;font-size:15px;letter-spacing:3.2px;margin-top:8px}
  .watermark{position:absolute;left:135px;top:410px;color:var(--watermark);font-weight:500;line-height:1;text-align:center;width:620px}
  .watermark span{display:block;font-size:150px;letter-spacing:-2px}
  .watermark small{display:block;font-size:38px;letter-spacing:12px;margin-top:14px}
  .content{position:absolute;left:91px;top:0;width:704px;font-size:13.4px;line-height:19.3px}
  .date{position:absolute;top:292px}
  .recipient{position:absolute;top:349px}
  .recipient strong{font-weight:500;color:var(--ink-strong)}
  .salutation{position:absolute;top:466px}
  .body-text{position:absolute;top:505px;width:704px;text-align:justify}
  .body-text p{margin-bottom:15px}
  .sign-name{position:absolute;top:910px;font-weight:500;color:var(--ink-strong)}
  .signature{position:absolute;left:-20px;top:930px;font-family:"Great Vibes",cursive;font-size:38px;color:var(--signature);line-height:1}
  .sign-role{position:absolute;top:987px}
  .contact{position:absolute;left:91px;top:1062px;font-size:13.6px;color:var(--ink)}
  .contact-company{font-size:17.5px;font-weight:500;color:var(--accent);margin-bottom:10px}
  .contact-line{display:flex;align-items:center;height:22px;letter-spacing:0.3px}
  .contact-line svg{width:12px;height:12px;margin-right:10px;fill:var(--accent)}
  .label{color:var(--accent);margin-right:4px}
  .gap{width:14px}
</style>
</head>
<body>
<main class="letterhead">
  <svg class="side-rule" width="70" height="1200" viewBox="0 0 70 1200" aria-hidden="true">
    <polygon points="35,47 60,78 60,1123 35,1123" fill="var(--accent)"/>
    <rect x="35" y="1133" width="25" height="19" fill="var(--accent)"/>
  </svg>

  <div class="brand">
    <span class="brand-name">Bright Oak</span>
    <span class="brand-sub">CONVEYANCING</span>
  </div>

  <div class="watermark" aria-hidden="true">
    <span>Bright Oak</span>
    <small>CONVEYANCING</small>
  </div>

  <section class="content">
    <p class="date">30/20/2016</p>
    <p class="recipient"><strong>Mr. XYZ Smith</strong><br>123, Street No. 123,<br>City Name<br>Pincode-123456</p>
    <p class="salutation">Dear Sir,</p>
    <div class="body-text">
      <p>Lorem Ipsum is simply dummy text of the printing and typesetting industry. Lorem Ipsum has been the industry's standard dummy text ever since the 1500s, when an unknown printer took a galley of type and scrambled it to make a type specimen book. It has survived not only five centuries, but also the leap into electronic typesetting, remaining essentially unchanged. It was popularised in the 1960s with the release of Letraset sheets containing Lorem Ipsum passages, and more recently with desktop publishing software like Aldus PageMaker including versions of Lorem Ipsum.</p>
      <p>Lorem Ipsum is simply dummy text of the printing and typesetting industry. Lorem Ipsum has been the industry's standard dummy text ever since the 1500s, when an unknown printer took a galley of type and scrambled it to make a type specimen book. It has survived not only five centuries, but also the leap into electronic typesetting, remaining essentially unchanged. It was popularised in the 1960s with the release of Letraset sheets containing Lorem Ipsum passages, and more recently with desktop publishing software like Aldus PageMaker including versions of Lorem Ipsum.</p>
      <p>Lorem Ipsum is simply dummy text of the printing and typesetting industry. Lorem Ipsum has been the industry's standard dummy text ever since the 1500s, when an unknown printer took a galley of type and scrambled it to make a type specimen book.</p>
    </div>
    <p class="sign-name">Your Name</p>
    <p class="signature">Your Signature</p>
    <p class="sign-role">CEO &nbsp;|&nbsp; Owner</p>
  </section>

  <footer class="contact">
    <p class="contact-company">Bright Oak Conveyancing Pty Ltd</p>
    <p class="contact-line">
      <svg viewBox="0 0 24 24" aria-hidden="true"><path d="M6.6 10.8c1.4 2.8 3.8 5.1 6.6 6.6l2.2-2.2c.3-.3.7-.4 1-.2 1.1.4 2.3.6 3.6.6.6 0 1 .4 1 1V20c0 .6-.4 1-1 1C10.6 21 3 13.4 3 4c0-.6.4-1 1-1h3.5c.6 0 1 .4 1 1 0 1.3.2 2.5.6 3.6.1.3 0 .7-.2 1z"/></svg>
      0461 739 286<span class="gap"></span>
      <svg viewBox="0 0 24 24" aria-hidden="true"><path d="M9 2h2v6h2V2h2v6h5v2h-5v4h5v2h-5v6h-2v-6h-2v6H9v-6H4v-2h5v-4H4V8h5zm2 8v4h2v-4z"/></svg>
      <span class="label">ACN</span>583 217 469
    </p>
    <p class="contact-line">
      <svg viewBox="0 0 24 24" aria-hidden="true"><path d="M12 2a10 10 0 1 0 0 20 10 10 0 0 0 0-20zm6.9 6h-3a15 15 0 0 0-1.3-3.9A8 8 0 0 1 18.9 8zM12 4c.8 1.2 1.5 2.5 1.9 4h-3.8c.4-1.5 1.1-2.8 1.9-4zM4.3 14a8 8 0 0 1 0-4h3.4a16 16 0 0 0 0 4zm.8 2h3a15 15 0 0 0 1.3 3.9A8 8 0 0 1 5.1 16zm3-8h-3a8 8 0 0 1 4.3-3.9C8.8 5.3 8.4 6.6 8.1 8zM12 20c-.8-1.2-1.5-2.5-1.9-4h3.8c-.4 1.5-1.1 2.8-1.9 4zm2.3-6H9.7a14 14 0 0 1 0-4h4.6a14 14 0 0 1 0 4zm.3 5.9c.6-1.2 1-2.5 1.3-3.9h3a8 8 0 0 1-4.3 3.9zm1.7-5.9a16 16 0 0 0 0-4h3.4a8 8 0 0 1 0 4z"/></svg>
      www.brightoakconveyancing.com.au
    </p>
    <p class="contact-line">
      <svg viewBox="0 0 24 24" aria-hidden="true"><path d="M12 2a7 7 0 0 0-7 7c0 5.2 7 13 7 13s7-7.8 7-13a7 7 0 0 0-7-7zm0 9.5a2.5 2.5 0 1 1 0-5 2.5 2.5 0 0 1 0 5z"/></svg>
      PO Box 871 Marlowdale SA 5096
    </p>
  </footer>
</main>
</body>
</html>
```